VELMOR Website Design

We need a website designed for our company VELMOR. We are a luxury lifestyle club that will provide benefits and services for our members. The site should be clean & sleek, preferably using black and white (or darker colors). (example sites: stravenhall.example, plinth.example)

Here is a link of a sample page I did using wix. (https://dunmere7.sitehostly.example/mysite) This can be used to get a general idea.

Target Market(s)

Upper Middle Class in the United States

Number of Pages Required

5+ page

Font styles to use
Sans Serif
Other font styles liked:
• Arial (or other similar fonts)

Requirements
Must have
• A clean design that is eye-catching and speaks to our company.
Nice to have
• Ideas for copy.

```html
<!DOCTYPE html>
<html lang="en">
<head>
<meta charset="utf-8">
<title>About VELMOR</title>
<link rel="stylesheet" href="https://fonts.googleapis.com/css2?family=Montserrat:wght@300;400;500;600&display=swap">
<style>
  :root {
    --ink-deep: #070c1a;
    --panel: rgba(12, 18, 34, 0.86);
    --text: #ffffff;
    --text-soft: #e4e6ec;
    --icon: #9a9ea8;
  }
  * { margin: 0; padding: 0; box-sizing: border-box; }
  html, body { width: 1200px; height: 977px; overflow: hidden; }
  body {
    position: relative;
    background: var(--ink-deep);
    color: var(--text);
    font-family: "Montserrat", Arial, sans-serif;
  }
  .site-header {
    position: absolute; left: 0; top: 0; width: 1200px; height: 97px;
    background: var(--ink-deep);
  }
  .brand {
    position: absolute; left: 150px; top: 30px;
    font-size: 32px; font-weight: 400; letter-spacing: 0.04em;
  }
  .main-nav {
    position: absolute; top: 41px; left: 613px;
    display: flex; gap: 26px;
    font-size: 12.5px; font-weight: 400; letter-spacing: 0.03em;
  }
  .main-nav a { color: var(--text-soft); text-decoration: none; }
  .main-nav a.is-current { color: var(--text); font-weight: 600; }
  .hero-photo {
    position: absolute; left: 0; top: 97px; width: 1200px; height: 801px;
    background:
      radial-gradient(ellipse at 30% 85%, rgba(170,110,95,0.55), transparent 45%),
      radial-gradient(ellipse at 80% 20%, rgba(110,135,150,0.5), transparent 50%),
      linear-gradient(180deg, #51606a 0%, #2d3848 50%, #4a4545 100%);
  }
  .about-panel {
    position: absolute; left: 75px; top: 162px; width: 1050px; height: 652px;
    background: var(--panel);
  }
  .about-title {
    position: absolute; left: 136px; top: 206px;
    font-weight: 300; line-height: 48px;
  }
  .about-title .lead { display: block; font-size: 50px; }
  .about-title .name { display: block; font-size: 48px; font-weight: 400; letter-spacing: 0.05em; }
  .tagline {
    position: absolute; left: 136px; top: 344px;
    font-size: 21px; font-weight: 400; letter-spacing: 0.3em;
  }
  .about-copy {
    position: absolute; left: 136px; top: 405px; width: 830px;
    font-size: 15px; line-height: 26px; letter-spacing: 0.13em; color: var(--text-soft);
  }
  .about-copy p + p { margin-top: 27px; }
  .apply-button {
    position: absolute; left: 136px; top: 727px; width: 143px; height: 44px;
    border: 2px solid var(--text); border-radius: 22px;
    display: flex; align-items: center; justify-content: center;
    font-size: 14px; font-weight: 600; color: var(--text); text-decoration: none;
  }
  .site-footer {
    position: absolute; left: 0; top: 897px; width: 1200px; height: 80px;
    background: var(--ink-deep); text-align: center;
  }
  .footer-title { margin-top: 20px; font-size: 12px; font-weight: 600; letter-spacing: 0.02em; }
  .social-links { display: flex; justify-content: center; gap: 12px; margin-top: 8px; }
  .social-dot { width: 14px; height: 14px; border-radius: 50%; background: var(--icon); }
</style>
</head>
<body>
  <header class="site-header">
    <div class="brand">VELMOR</div>
    <nav class="main-nav">
      <a href="#">HOME</a>
      <a href="#" class="is-current">ABOUT</a>
      <a href="#">SERVICES AND BENEFITS</a>
      <a href="#">APPLY</a>
      <a href="#">CONTACT</a>
    </nav>
  </header>

  <div class="hero-photo" role="img" aria-label="Blurred photo of two hands toasting with wine glasses at a dinner table"></div>

  <section class="about-panel" aria-hidden="true"></section>
  <h1 class="about-title"><span class="lead">About</span><span class="name">VELMOR</span></h1>
  <p class="tagline">The ultimate full service lifestyle club</p>
  <div class="about-copy">
    <p>VELMOR was formed to bring the best services, experiences, and exclusive opportuni-ties to our members.</p>
    <p>With everything from private member events to pirvate jet travel, the persk of being a VELMOR member are unmatched.</p>
    <p>Professional athletes, artists, musicians, corporate professionals: Our members come from diverse backgrounds.</p>
    <p>Comprehensive services like 24/7 conceirge, accountants, attorneys, private advisers, planners, investment advisors and more.</p>
  </div>
  <a href="#" class="apply-button">Apply</a>

  <footer class="site-footer">
    <div class="footer-title">CONTACT US</div>
    <div class="social-links">
      <span class="social-dot"></span>
      <span class="social-dot"></span>
      <span class="social-dot"></span>
      <span class="social-dot"></span>
      <span class="social-dot"></span>
    </div>
  </footer>
</body>
</html>
```